New iOS App design for Boston Startup

We are looking for a new app design for our iPhone app. The current app's design feels outdated and we like to add lots of new functionality and a new navigation as well. A complete overhaul therefore!
We want you to design 5 screens that will have changed the most. The complete wireframes of these 5 pages are attached in the requirements document.
Once the winning design is selected we will award the winner with the designing all other screens (40-50 screens based on the same design). This will be a separate project worth $1000. The winning designer can get more follow up work if both sides are happy about the cooperation.
We will give feedback as soon as the first screen has been uploaded for review. Final decision will be made only after all 5 screens are finished.
We hope you give it your best!
Note: will only communicate through PixelHarbor (no skype),
Updates
Reason: Want to give designers a chance to submit their designs as I understand from some, the deadline is too close.
I have raised the award and introduced a 2nd price as well to make it worth your time. I hope you give it your best shot.
Reason: A few of you have asked for an extension of the deadline as time is running out. I will extend by one day. Tell me if you need more.
Industry/Entity Type
Startup
Requirements
Must have
- At least 1 screen before we can give you feedback.
Nice to have
- multiple options of 1 screen to get to a desirable design

```html
<!DOCTYPE html>
<html lang="en">
<head>
<meta charset="utf-8">
<title>Home — Study Dashboard</title>
<link href="https://fonts.googleapis.com/css2?family=Open+Sans:wght@400;600;700&display=swap" rel="stylesheet">
<style>
:root{
  --teal:#0a9b7d;
  --teal-light:#6cc6b3;
  --gauge-grey:#a8a8a8;
  --paper:#efefed;
  --ink:#111111;
  --muted:#666666;
  --band:#cfcfcf;
  --band-line:#b2b2b2;
  --purple:#c64df0;
  --tab:#8e8e8e;
  --white:#ffffff;
  --up:#3fae3a;
}
*{box-sizing:border-box;margin:0;padding:0}
html,body{width:676px;height:1200px;overflow:hidden;background:var(--paper)}
body{font-family:"Open Sans",Arial,sans-serif;color:var(--ink)}
.screen{position:relative;width:640px;height:1136px;transform:scale(1.05625);transform-origin:0 0;background:var(--paper)}
.status-bar{position:absolute;left:0;top:0;width:640px;height:40px;background:#000;color:var(--white);font-weight:600;font-size:24px;display:flex;align-items:center;padding:0 12px}
.status-bar .carrier{margin-left:6px}
.status-bar .time{position:absolute;left:0;right:0;text-align:center}
.status-bar .battery{position:absolute;right:10px;top:10px}
.menu-button{position:absolute;left:24px;top:68px}
.welcome{position:absolute;left:80px;right:20px;top:58px;text-align:center;font-size:35px;font-weight:700;letter-spacing:2px;color:var(--muted)}
.gauge{position:absolute;left:0;top:0}
.score{position:absolute;left:232px;top:238px;width:146px;text-align:center;font-weight:700}
.score .value{font-size:40px;letter-spacing:2px;line-height:48px}
.score .delta{font-size:24px;letter-spacing:2px;line-height:30px}
.score-label{position:absolute;left:200px;width:200px;top:352px;text-align:center;font-weight:700;font-size:23px;letter-spacing:2px;line-height:35px}
.stats-band{position:absolute;left:0;top:430px;width:640px;height:122px;background:var(--band)}
.stat{position:absolute;top:0;height:122px;text-align:center;color:#333}
.stat .num{position:absolute;top:24px;font-size:27px;white-space:nowrap}
.stat .label{position:absolute;top:78px;font-size:26px;color:#444;white-space:nowrap}
.divider{position:absolute;top:0;width:2px;height:122px;background:var(--band-line)}
.up{display:inline-block;vertical-align:-2px}
.nav-list{position:absolute;left:70px;top:581px;width:500px}
.nav-item{display:flex;align-items:center;justify-content:space-between;background:var(--purple);color:var(--white);font-size:24px;padding:0 22px 0 32px;border-bottom:2px solid #e6c4f4}
.nav-item:last-child{border-bottom:none}
.up-next{position:absolute;left:70px;top:853px}
.up-next-text{position:absolute;left:70px;top:886px;width:430px;text-align:center;color:var(--white)}
.up-next-text .kicker{font-size:22px;line-height:34px}
.up-next-text .lesson{font-size:29px;line-height:38px}
.tab-bar{position:absolute;left:43px;top:1040px;width:562px;height:80px}
.tab{position:absolute;top:0;width:92px;height:80px;background:var(--tab);color:var(--white);font-size:17px;text-align:center}
.tab svg{display:block;margin:6px auto 0}
.tab .tab-name{position:absolute;left:0;right:0;bottom:2px}
.tab.active{background:var(--white);border:2px solid #999;width:114px;top:-20px;height:100px;color:#8a3fd6}
.tab.active svg{margin-top:24px}
</style>
</head>
<body>
<div class="screen">
  <header class="status-bar">
    <svg width="36" height="18" viewBox="0 0 36 18"><g fill="#fff"><rect x="0" y="12" width="5" height="6"/><rect x="7" y="9" width="5" height="9"/><rect x="14" y="6" width="5" height="12"/><rect x="21" y="3" width="5" height="15"/><rect x="28" y="0" width="5" height="18"/></g></svg>
    <span class="carrier">ORBIT &nbsp;3G</span>
    <span class="time">9:51 PM</span>
    <svg class="battery" width="86" height="22" viewBox="0 0 86 22"><circle cx="11" cy="11" r="9" fill="none" stroke="#fff" stroke-width="3"/><path d="M11 5v6h4" stroke="#fff" stroke-width="2" fill="none"/><rect x="32" y="2" width="46" height="18" rx="3" fill="none" stroke="#fff" stroke-width="2"/><rect x="35" y="5" width="40" height="12" fill="#fff"/><rect x="79" y="7" width="4" height="8" fill="#fff"/></svg>
  </header>

  <svg class="menu-button" width="46" height="36" viewBox="0 0 46 36" aria-label="Menu"><g fill="var(--teal)"><rect y="0" width="46" height="7" rx="3"/><rect y="14" width="46" height="7" rx="3"/><rect y="28" width="46" height="7" rx="3"/></g></svg>
  <h1 class="welcome">Welcome back, Noam!</h1>

  <svg class="gauge" width="640" height="430" viewBox="0 0 640 430">
    <path d="M217 353 A128 128 0 1 1 413 191" fill="none" stroke="var(--teal)" stroke-width="24"/>
    <path d="M413 191 A128 128 0 0 1 384 361" fill="none" stroke="var(--gauge-grey)" stroke-width="24"/>
    <circle cx="305" cy="270" r="73" fill="var(--teal)"/>
    <path d="M233 256 A73 73 0 0 1 377 256 Z" fill="var(--teal-light)"/>
  </svg>
  <div class="score"><div class="value">640</div><div class="delta">↓-18</div></div>
  <div class="score-label">YOUR<br>SCORE!</div>

  <section class="stats-band">
    <svg style="position:absolute;left:0;top:46px" width="16" height="28" viewBox="0 0 16 28"><path d="M0 2 L14 14 L0 26" fill="none" stroke="#fff" stroke-width="5"/></svg>
    <div class="stat"><span class="num" style="left:64px">34%<svg class="up" width="18" height="26" viewBox="0 0 18 26"><path d="M9 0 L18 11 H12 V26 H6 V11 H0 Z" fill="var(--up)"/></svg> +4</span><span class="label" style="left:58px">Completion</span></div>
    <div class="divider" style="left:227px"></div>
    <div class="stat"><span class="num" style="left:240px">20<svg class="up" width="18" height="26" viewBox="0 0 18 26"><path d="M9 0 L18 11 H12 V26 H6 V11 H0 Z" fill="var(--up)"/></svg>+3</span><span class="label" style="left:259px">Sessions</span></div>
    <div class="stat"><span class="num" style="left:371px">18<svg class="up" width="18" height="26" viewBox="0 0 18 26"><path d="M9 0 L18 11 H12 V26 H6 V11 H0 Z" fill="var(--up)"/></svg>+10</span><span class="label" style="left:389px">Min.</span></div>
    <div class="divider" style="left:497px"></div>
    <div class="stat"><span class="label" style="left:511px">This week</span></div>
    <svg style="position:absolute;left:622px;top:40px" width="18" height="30" viewBox="0 0 18 30"><path d="M18 2 L4 15 L18 28" fill="none" stroke="#fff" stroke-width="5"/></svg>
  </section>

  <nav class="nav-list">
    <div class="nav-item" style="height:83px">Analytics<svg width="28" height="30" viewBox="0 0 28 30"><path d="M4 3 L22 15 L4 27" fill="none" stroke="#fff" stroke-width="6"/></svg></div>
    <div class="nav-item" style="height:82px">Course Overview<svg width="28" height="30" viewBox="0 0 28 30"><path d="M4 3 L22 15 L4 27" fill="none" stroke="#fff" stroke-width="6"/></svg></div>
    <div class="nav-item" style="height:77px;padding-left:30px">Days until test 33<svg width="28" height="30" viewBox="0 0 28 30"><path d="M4 3 L22 15 L4 27" fill="none" stroke="#fff" stroke-width="6"/></svg></div>
  </nav>

  <svg class="up-next" width="504" height="128" viewBox="0 0 504 128"><path d="M0 20 H425 V0 L502 64 L425 127 V109 H0 Z" fill="var(--teal)"/></svg>
  <div class="up-next-text"><div class="kicker">Up Next: Sentence Correction</div><div class="lesson">Lesson 4</div></div>

  <nav class="tab-bar">
    <div class="tab" style="left:0"><svg width="56" height="44" viewBox="0 0 56 44"><path d="M4 6 Q16 2 28 8 Q40 2 52 6 V40 Q40 36 28 42 Q16 36 4 40 Z M28 8 V42" fill="none" stroke="#fff" stroke-width="3"/></svg><span class="tab-name">Theory</span></div>
    <div class="tab" style="left:109px"><svg width="50" height="44" viewBox="0 0 50 44"><rect x="3" y="3" width="44" height="38" fill="none" stroke="#fff" stroke-width="3"/><g fill="#fff"><rect x="8" y="10" width="34" height="4"/><rect x="8" y="20" width="34" height="4"/><rect x="8" y="30" width="34" height="4"/></g></svg><span class="tab-name">Practice</span></div>
    <div class="tab active" style="left:221px"><svg width="52" height="44" viewBox="0 0 52 44"><path d="M26 2 L50 22 H43 V42 H31 V30 H21 V42 H9 V22 H2 Z" fill="#8a3fd6"/></svg><span class="tab-name">Home</span></div>
    <div class="tab" style="left:357px"><svg width="46" height="46" viewBox="0 0 46 46"><rect x="2" y="2" width="42" height="42" rx="6" fill="#fff"/><g fill="#666"><circle cx="12" cy="12" r="4"/><circle cx="34" cy="12" r="4"/><circle cx="23" cy="23" r="4"/><circle cx="12" cy="34" r="4"/><circle cx="34" cy="34" r="4"/></g></svg><span class="tab-name">Games</span></div>
    <div class="tab" style="left:468px"><svg width="50" height="46" viewBox="0 0 50 46"><rect x="3" y="10" width="34" height="34" fill="none" stroke="#fff" stroke-width="3"/><path d="M10 24 L20 34 L46 4" fill="none" stroke="#fff" stroke-width="6"/></svg><span class="tab-name">Test</span></div>
  </nav>
</div>
</body>
</html>
```